Business Card Design Project

We are a construction company in Orange County, CA. We need a two sided business card. We would like the back to be our logo with web URL. Front should included Name, title, address, phone, fax and email address.

our address is
627 West Dorrance Blvd, Suite 308
Anaheim, CA 92718

Our logo files are attached.

Construction

```html
<!DOCTYPE html>
<html lang="en">
<head>
<meta charset="utf-8">
<title>Keystar Business Card</title>
<link href="https://fonts.googleapis.com/css2?family=Source+Sans+3:wght@400;600;700;900&display=swap" rel="stylesheet">
<style>
  :root {
    --brand-blue: #154b7e;
    --ink: #3a3a3a;
    --ink-soft: #4a4a4a;
    --divider: #b5b5b5;
    --card: #ffffff;
    --backdrop: #e6e7e9;
    --swoosh-light: #e4e5e7;
    --swoosh-dark: #8e9093;
  }
  html, body {
    margin: 0;
    padding: 0;
    width: 960px;
    height: 1200px;
    overflow: hidden;
    background: var(--backdrop);
    font-family: "Source Sans 3", sans-serif;
  }
  .canvas {
    position: relative;
    width: 960px;
    height: 1200px;
  }
  .card {
    position: absolute;
    width: 840px;
    height: 478px;
    background: var(--card);
    border-radius: 28px;
    overflow: hidden;
    box-shadow: 0 4px 10px rgba(0,0,0,0.18);
  }
  .card--front { left: 50px; top: 95px; }
  .card--back  { left: 55px; top: 645px; }

  .card__waves {
    position: absolute;
    left: 0; top: 0;
    width: 840px;
    height: 478px;
  }

  .brand-name {
    position: absolute;
    margin: 0;
    color: var(--brand-blue);
    font-weight: 900;
    line-height: 1;
    letter-spacing: 1px;
  }
  .card--front .brand-name {
    left: 50px;
    top: 93px;
    font-size: 96px;
  }
  .card--back .brand-name {
    left: 0;
    width: 840px;
    top: 143px;
    text-align: center;
    font-size: 150px;
  }

  .divider {
    position: absolute;
    left: 521px;
    top: 85px;
    width: 2px;
    height: 117px;
    background: var(--divider);
  }

  .person {
    position: absolute;
    left: 546px;
    top: 93px;
    color: var(--ink);
  }
  .person__name {
    margin: 0;
    font-size: 34px;
    font-weight: 600;
    line-height: 1.1;
  }
  .person__title {
    margin: 4px 0 12px;
    font-size: 21px;
    font-weight: 600;
    color: var(--ink-soft);
  }
  .contact-line {
    margin: 0;
    font-size: 21px;
    line-height: 28px;
    color: var(--ink-soft);
  }
  .contact-line__label {
    font-weight: 700;
    font-style: italic;
    color: var(--ink);
  }

  .online {
    position: absolute;
    left: 50px;
    top: 292px;
  }

  .address {
    position: absolute;
    left: 0;
    width: 840px;
    top: 425px;
    margin: 0;
    text-align: center;
    color: #ffffff;
    font-size: 24px;
    line-height: 30px;
  }

  .website {
    position: absolute;
    left: 0;
    width: 840px;
    top: 398px;
    margin: 0;
    text-align: center;
    font-size: 31px;
    font-weight: 700;
    color: var(--ink);
  }
</style>
</head>
<body>
<main class="canvas">

  <section class="card card--front" aria-label="Business card front">
    <svg class="card__waves" viewBox="0 0 840 478" aria-hidden="true">
      <defs>
        <linearGradient id="swoosh" x1="0" y1="0" x2="1" y2="0">
          <stop offset="0" stop-color="var(--swoosh-light)"/>
          <stop offset="0.6" stop-color="var(--swoosh-dark)"/>
          <stop offset="1" stop-color="#c9cacc"/>
        </linearGradient>
      </defs>
      <path fill="url(#swoosh)" d="M555,398 C680,392 800,340 840,253 L840,300 C790,362 690,395 555,398 Z"/>
      <path fill="var(--brand-blue)" d="M0,430 C120,388 230,374 330,384 C430,394 520,406 600,401 C700,394 790,362 840,318 L840,478 L0,478 Z"/>
    </svg>

    <h1 class="brand-name">KEYSTAR</h1>
    <div class="divider"></div>

    <div class="person">
      <p class="person__name">Your Name</p>
      <p class="person__title">Designation</p>
      <p class="contact-line"><span class="contact-line__label">p</span> : 1-234-4567</p>
      <p class="contact-line"><span class="contact-line__label">f</span> : 1-234-4567</p>
    </div>

    <div class="online">
      <p class="contact-line"><span class="contact-line__label">e</span> : info@keystarmail.com</p>
      <p class="contact-line"><span class="contact-line__label">w</span> : www.keystarbuild.com</p>
    </div>

    <p class="address">627 West Dorrance Blvd, Suite 308, Anaheim, CA 92718</p>
  </section>

  <section class="card card--back" aria-label="Business card back">
    <h2 class="brand-name">KEYSTAR</h2>
    <p class="website">www.keystarbuild.com</p>
  </section>

</main>
</body>
</html>
```